Investor Slide Deck

Simple idea - take a model investor deck and build out a investor deck for K7V. I will complete the data, I need a template to work from within. I will attach a model investor deck and a blank K7V that I need built out to K7V. Use the K7V Pwrpt to build out the investor deck

```html
<!DOCTYPE html>
<html lang="en">
<head>
<meta charset="utf-8">
<title>K7V Investor Deck</title>
<link href="https://fonts.googleapis.com/css2?family=Nunito+Sans:wght@400;600;700;800&display=swap" rel="stylesheet">
<style>
:root{
  --orange:#f4561a;
  --orange-soft:#fde3d8;
  --teal:#1e6b85;
  --teal-card:#2f7890;
  --aqua:#1fb3a4;
  --green:#8dbf00;
  --yellow:#fbbf2c;
  --ink:#222;
  --muted:#555;
  --page:#bdbdbd;
}
*{box-sizing:border-box;margin:0;padding:0}
html,body{width:1036px;height:1200px;overflow:hidden;background:var(--page);font-family:"Nunito Sans",sans-serif;color:var(--ink)}
.deck{position:relative;width:1036px;height:1200px}
.slide{position:absolute;width:488px;height:275px;overflow:hidden;background:#fff}
.col-a{left:21px}.col-b{left:527px}
.row-1{top:24px}.row-2{top:317px}.row-3{top:610px}.row-4{top:900px}
.slide-foot{position:absolute;left:0;bottom:0;width:100%;height:16px;background:var(--teal);color:#fff;font-size:4.5px;font-weight:600;text-align:center;line-height:16px}
.slide-title{position:absolute;left:16px;top:13px;font-size:15px;font-weight:800;color:var(--orange);letter-spacing:.3px}
.brand-mark{position:absolute;right:16px;top:10px;font-size:14px;font-weight:800;color:var(--orange);letter-spacing:.5px}
.soft-bg{position:absolute;inset:0;background:linear-gradient(180deg,#f3f5f7 0%,#e7ebef 60%,#dfe4e9 100%)}
.photo-circle{position:absolute;width:176px;height:176px;border-radius:50%}
.arc{position:absolute}

/* Welcome */
.welcome-logo{left:259px;top:68px;font-size:22px;top:62px;position:absolute;font-weight:800;color:var(--orange)}
.welcome-title{position:absolute;left:259px;top:116px;font-size:17px;font-weight:800;color:#333}
.welcome-title span{color:var(--orange)}
.welcome-body{position:absolute;left:259px;top:145px;width:182px;font-size:7.6px;line-height:12.2px;color:#333}

/* Problems */
.intro{position:absolute;left:16px;top:44px;width:395px;font-size:7.4px;line-height:12.4px;color:#333}
.problem{position:absolute;top:82px;width:86px;height:142px;border-radius:6px;text-align:center;padding:0 5px}
.problem .icon{width:42px;height:42px;border-radius:50%;margin:20px auto 0;display:flex;align-items:center;justify-content:center}
.problem h3{font-size:7.2px;font-weight:600;line-height:9.4px;margin-top:6px}
.problem p{font-size:4.6px;line-height:8.1px;color:#444;margin-top:6px}

/* Business model */
.model-card{position:absolute;top:53px;width:201px;height:184px;border-radius:6px;color:#fff;padding:2px}
.model-card .media{height:102px;border-radius:5px}
.model-card h3{font-size:9px;font-weight:700;margin:9px 6px 0;line-height:11px}
.model-card p{font-size:5.4px;line-height:9.6px;margin:4px 6px 0}

/* Segments */
.segment{position:absolute;top:59px;width:111px;height:158px;border-radius:5px;overflow:hidden}
.segment .media{height:100px}
.segment .label{height:58px;display:flex;align-items:center;justify-content:center;text-align:center;color:#fff;font-size:7px;font-weight:700;line-height:10px;padding:0 8px}

/* Markets */
.market-box{position:absolute;left:16px;top:41px;width:228px;height:202px;background:#eeeded}
.market-text{position:absolute;font-size:7.4px;line-height:11.7px;color:#222}

/* Competitive */
.group-title{position:absolute;font-size:9.2px;font-weight:700;transform:translateX(-50%);white-space:nowrap}
.firm{position:absolute;width:86px;height:32px;background:#fff;border-radius:4px;box-shadow:0 1px 3px rgba(0,0,0,.18);display:flex;align-items:center;justify-content:center;font-size:7px;font-weight:700;color:var(--teal)}

/* Contact */
.contact-row{position:absolute;left:52px;display:flex;align-items:center;gap:10px;font-size:6.8px;font-weight:700;line-height:9px}
.contact-row .pin{width:28px;height:28px;border-radius:50%;background:var(--orange);display:flex;align-items:center;justify-content:center;flex:none}
</style>
</head>
<body>
<main class="deck">

  <!-- Welcome -->
  <section class="slide col-a row-1">
    <div class="soft-bg" role="img" aria-label="Faded photo of a large solar panel field in sunlight"></div>
    <div class="photo-circle" style="left:35px;top:39px;background:linear-gradient(160deg,#6f8aa6,#3d5568 55%,#7a8b55)" role="img" aria-label="Engineer in a safety vest holding a clipboard beside solar panels"></div>
    <svg class="arc" style="left:66px;top:200px" width="114" height="22" viewBox="0 0 114 22"><path d="M3 4 Q57 30 111 4" fill="none" stroke="var(--aqua)" stroke-width="5" stroke-linecap="round"/></svg>
    <div class="welcome-logo">K7V</div>
    <h1 class="welcome-title">Welcome To <span>K7V</span></h1>
    <p class="welcome-body">Sed ut perspiciatis unde omnis iste natus error sit voluptatem accusantium doloremque laudantium, totam rem aperiam, eaque ipsa quae ab illo inventore veritatis et quasi architecto beatae vitae dicta sunt explicabo.</p>
    <div class="slide-foot">Private &amp; Confidential | 2024</div>
  </section>

  <!-- Problems -->
  <section class="slide col-b row-1">
    <h2 class="slide-title">PROBLEMS</h2>
    <div class="brand-mark">K7V</div>
    <p class="intro">Every year, the rise in prices of electricity is burning a hole in the pocket of consumers. Solar Power is a reliable solution, but the industry is facing its own set of challenges</p>

    <div class="problem" style="left:16px;background:var(--orange-soft)">
      <div class="icon" style="background:var(--orange)"><svg width="22" height="22" viewBox="0 0 24 24" fill="none" stroke="#fff" stroke-width="1.6"><circle cx="12" cy="9" r="6"/><path d="M12 6l1 2 2 .3-1.5 1.4.4 2.1-1.9-1-1.9 1 .4-2.1L9 8.3l2-.3z"/><path d="M8 14l-2 7 3-1.5 2 2 1-4M16 14l2 7-3-1.5-2 2-1-4"/></svg></div>
      <h3 style="color:var(--orange)">Poor Quality<br>Components</h3>
      <p>The use of low-quality solar panels and components in solar plant construction is impacting their efficiency and lifespan.</p>
    </div>
    <div class="problem" style="left:108px;background:#e4eef1">
      <div class="icon" style="background:var(--teal)"><svg width="22" height="22" viewBox="0 0 24 24" fill="none" stroke="#fff" stroke-width="1.6"><path d="M4 20l9-9M14 4a4 4 0 0 0 5 5l-3 3-5-5z"/><path d="M5 4l4 4-2 2-4-4zM13 13l6 6-2 2-6-6"/></svg></div>
      <h3 style="color:var(--teal)">Poor<br>Installation</h3>
      <p>Solar plant installations demand precision; poor installation can lead to downtime, damage, and efficiency loss.</p>
    </div>
    <div class="problem" style="left:200px;background:#efece6">
      <div class="icon" style="background:var(--yellow);margin-top:16px"><svg width="22" height="22" viewBox="0 0 24 24" fill="none" stroke="#333" stroke-width="1.5"><path d="M9 17h6v-2a6 6 0 1 0-6 0z"/><path d="M10 20h4M12 2v2M4 10H2M22 10h-2M5 4l1.5 1.5M19 4l-1.5 1.5"/><circle cx="12" cy="10" r="2"/></svg></div>
      <h3 style="color:var(--yellow)">Lack of<br>Awareness</h3>
      <p>Limited awareness of government subsidies and inadequate financing options for high-cost solar plant purchases can lead to missed product benefits</p>
    </div>
    <div class="problem" style="left:292px;background:#e6f3f1">
      <div class="icon" style="background:var(--aqua);margin-top:12px"><svg width="22" height="22" viewBox="0 0 24 24" fill="none" stroke="#333" stroke-width="1.5"><path d="M3 8l7-4 7 4v8l-7 4-7-4z"/><path d="M3 8l7 4 7-4M10 12v8"/><circle cx="19" cy="16" r="3"/></svg></div>
      <h3 style="color:var(--aqua)">Unreliable Customer and Warranty Support</h3>
      <p>Challenges in reaching timely support and clarifying warranty terms can result in customer frustration and self-reliance for issue</p>
    </div>
    <div class="problem" style="left:384px;background:var(--orange-soft)">
      <div class="icon" style="background:var(--orange);margin-top:12px"><svg width="22" height="22" viewBox="0 0 24 24" fill="none" stroke="#fff" stroke-width="1.6"><path d="M12 3l7 7-9 9-7-7V3z"/><circle cx="8" cy="8" r="1.5"/><path d="M14 14l3 3"/></svg></div>
      <h3 style="color:var(--orange)">Lack of Transparency in Pricing and Performance</h3>
      <p>Customers might encounter unexpected hidden costs during installation and lower energy generation than initially agreed upon</p>
    </div>
    <div class="slide-foot">Private &amp; Confidential | 2024</div>
  </section>

  <!-- Business model -->
  <section class="slide col-a row-2">
    <div class="soft-bg" style="opacity:.5"></div>
    <h2 class="slide-title">BUSINESS MODEL</h2>
    <div class="brand-mark">K7V</div>
    <div class="model-card" style="left:23px;background:var(--green)">
      <div class="media" style="background:#fff;display:flex;align-items:center;justify-content:center"><div style="width:100px;height:70px;background:linear-gradient(135deg,#1e2a4f,#2f3d6b)" role="img" aria-label="Ground-mounted solar panel array"></div></div>
      <h3>SALES OF SOLAR PANEL</h3>
      <p>Solar Panels manufactured at our manufacturing facility will be sold via different channels that we will develop. We aim to reach out to B2C customers via a separate franchise model that we will begin after commencement of manufacturing operations.</p>
    </div>
    <div class="model-card" style="left:234px;background:var(--teal-card)">
      <div class="media" style="background:linear-gradient(170deg,#7fa35a 0%,#9fb0bd 35%,#4a5c88 100%)" role="img" aria-label="Aerial view of a utility-scale solar farm"></div>
      <h3>GOVERNMENT AND INDUSTRIAL EPC PROJECTS</h3>
      <p>We project about half of our manufactured solar panels to be used in EPC projects that we will bid for. We aim to generate gross margins of 10% - 12% on the overall projects.</p>
    </div>
    <div class="slide-foot">Private &amp; Confidential | 2024</div>
  </section>

  <!-- Segments -->
  <section class="slide col-b row-2">
    <h2 class="slide-title">OUR BUSINESS SEGMENTS</h2>
    <div class="brand-mark">K7V</div>
    <div class="segment" style="left:16px">
      <div class="media" style="background:linear-gradient(180deg,#b8c2cc,#8a97a5)" role="img" aria-label="Apartment buildings with rooftop solar"></div>
      <div class="label" style="background:var(--orange)">Residential House Owners And Housing Societies</div>
    </div>
    <div class="segment" style="left:131px">
      <div class="media" style="background:linear-gradient(160deg,#a0664a,#5b7a8f 60%,#c4834d)" role="img" aria-label="Aerial view of a shipping container port"></div>
      <div class="label" style="background:var(--teal)">Oems &amp; Exports</div>
    </div>
    <div class="segment" style="left:246px">
      <div class="media" style="background:linear-gradient(180deg,#6f7f95,#3b5283)" role="img" aria-label="Industrial rooftop covered with solar panels"></div>
      <div class="label" style="background:var(--yellow)">Industries</div>
    </div>
    <div class="segment" style="left:361px">
      <div class="media" style="background:linear-gradient(180deg,#a8c8e6 0%,#a8c8e6 30%,#3e5fa5 55%,#2b4a8f)" role="img" aria-label="Large utility solar park under a blue sky"></div>
      <div class="label" style="background:var(--orange)">Government Tenders And Utility Projects</div>
    </div>
    <div class="slide-foot">Private &amp; Confidential | 2024</div>
  </section>

  <!-- Target markets -->
  <section class="slide col-a row-3">
    <h2 class="slide-title">TARGET MARKETS</h2>
    <div class="brand-mark">K7V</div>
    <div class="market-box">
      <div style="position:absolute;left:22px;top:14px;width:98px;height:98px;background:linear-gradient(135deg,#1550a8 0%,#1550a8 50%,#f5e02a 65%,#d6d6d6 80%)" role="img" aria-label="Map of India with short and medium term states highlighted"></div>
    </div>
    <p class="market-text" style="left:30px;top:171px;width:205px">Short Term – Location, Maharashtra, MP, Maharashtra<br>• Medium Term – All Indian States with Solar Power Demand<br>• Setting up of Certification process for Export Markets</p>
    <div style="position:absolute;left:272px;top:52px;width:199px;height:101px;background:linear-gradient(90deg,#1151a3 0%,#e8ecef 45%,#f3d11b 60%,#e8ecef 75%,#1151a3 100%)" role="img" aria-label="World map highlighting the Middle East and Africa"></div>
    <p class="market-text" style="left:272px;top:168px;width:210px">• Long Term – India.<br>• Export Markets - Middle East and African Continent</p>
    <div class="slide-foot">Private &amp; Confidential | 2024</div>
  </section>

  <!-- Competitive analysis -->
  <section class="slide col-b row-3">
    <h2 class="slide-title">COMPETITIVE ANALYSIS</h2>
    <div class="brand-mark">K7V</div>
    <div class="group-title" style="left:130px;top:91px;color:var(--orange)">EPC Providers</div>
    <div class="group-title" style="left:359px;top:71px;color:var(--teal)">Solar Panel Manufacturers</div>
    <div class="firm" style="left:43px;top:123px">Brightfield Power</div>
    <div class="firm" style="left:138px;top:123px">Meridian Solar</div>
    <div class="firm" style="left:43px;top:164px">Sunvale</div>
    <div class="firm" style="left:138px;top:164px">Orrin Energy</div>
    <div class="firm" style="left:270px;top:103px">Helvion</div>
    <div class="firm" style="left:364px;top:103px">Tarsel</div>
    <div class="firm" style="left:270px;top:144px">Lumora</div>
    <div class="firm" style="left:364px;top:144px">Quenta Solar</div>
    <div class="firm" style="left:270px;top:184px">Ardent Solar</div>
    <div class="slide-foot">Private &amp; Confidential | 2024</div>
  </section>

  <!-- Appendix -->
  <section class="slide col-a row-4">
    <h2 class="slide-title">APPENDIX</h2>
    <div class="brand-mark">K7V</div>
    <div style="position:absolute;left:16px;top:31px;font-size:8px;font-weight:700">Solar Panel Manufacturing Plant Layout</div>
    <div style="position:absolute;left:17px;top:61px;width:443px;height:159px;background:linear-gradient(180deg,#fafafa,#ececec);border:1px solid #e0e0e0" role="img" aria-label="Technical floor plan of the solar panel manufacturing plant"></div>
    <div style="position:absolute;left:0;width:455px;text-align:center;top:232px;font-size:8px">Floor Plan</div>
    <div class="slide-foot">Private &amp; Confidential | 2024</div>
  </section>

  <!-- Contact -->
  <section class="slide col-b row-4">
    <div class="soft-bg" role="img" aria-label="Faded photo of a solar panel field"></div>
    <div style="position:absolute;left:52px;top:24px;font-size:22px;font-weight:800;color:var(--orange)">K7V</div>
    <div class="contact-row" style="top:80px">
      <span class="pin"><svg width="12" height="12" viewBox="0 0 24 24" fill="#fff"><path d="M12 2a7 7 0 0 0-7 7c0 5 7 13 7 13s7-8 7-13a7 7 0 0 0-7-7zm0 9.5A2.5 2.5 0 1 1 12 6.5a2.5 2.5 0 0 1 0 5z"/></svg></span>
      <span>25,k7vLorem ipsum dolor<br>sit amet, consectetur 253</span>
    </div>
    <div class="contact-row" style="top:116px">
      <span class="pin"><svg width="12" height="12" viewBox="0 0 24 24" fill="#fff"><path d="M6.6 10.8a15 15 0 0 0 6.6 6.6l2.2-2.2c.3-.3.7-.4 1-.2 1.1.4 2.3.6 3.6.6.6 0 1 .4 1 1V20c0 .6-.4 1-1 1A17 17 0 0 1 3 4c0-.6.4-1 1-1h3.5c.6 0 1 .4 1 1 0 1.3.2 2.5.6 3.6.1.3 0 .7-.2 1z"/></svg></span>
      <span>+1 555 010 2040</span>
    </div>
    <div class="contact-row" style="top:153px">
      <span class="pin"><svg width="12" height="12" viewBox="0 0 24 24" fill="#fff"><path d="M3 6h18v12H3z"/><path d="M3 6l9 7 9-7" stroke="var(--orange)" stroke-width="1.6" fill="none"/></svg></span>
      <span>info@k7v.com</span>
    </div>
    <div class="contact-row" style="top:189px">
      <span class="pin"><svg width="12" height="12" viewBox="0 0 24 24" fill="none" stroke="#fff" stroke-width="2"><circle cx="12" cy="12" r="9"/><path d="M3 12h18M12 3c3 3 3 15 0 18M12 3c-3 3-3 15 0 18"/></svg></span>
      <span>www.k7v.com</span>
    </div>
    <div class="photo-circle" style="left:278px;top:33px;background:linear-gradient(160deg,#3d4a2f,#4f8fa6 50%,#7c7a38)" role="img" aria-label="Solar panels among trees and grass"></div>
    <svg class="arc" style="left:309px;top:194px" width="114" height="22" viewBox="0 0 114 22"><path d="M3 4 Q57 30 111 4" fill="none" stroke="var(--aqua)" stroke-width="5" stroke-linecap="round"/></svg>
    <div class="slide-foot">Private &amp; Confidential | 2024</div>
  </section>

</main>
</body>
</html>
```